Golf Brochure + Business Card Design Project – Kestrel Fitness.

Task Description

We are looking for a premium tri-fold brochure (8.5x11 letter, folded) plus a new business card design for Kestrel Fitness. Both need to look polished, elegant, and professional — something that would feel at home in a golf club environment.

Brochure Scope:
• Tri-fold brochure promoting our new golf-specific services
• Incorporate brand colors: deep hunter green, cream, and gold accents
• Clean, modern typography (professional, not playful)
• Layout will follow the copy provided (final copy attached, no rewriting needed)
• Imagery: mature golfers (50+), golf lifestyle shots, no generic stocky images
• Include QR code placement linking to booking page
• Deliverables: print-ready PDF with bleed/crop (CMYK), high-res PDF (digital), and source file (InDesign or Illustrator)

Business Card Scope:
• Front + back design
• Consistent with brand colors and fonts
• Space for name, title, phone, email, and website
• Deliverables: print-ready PDF with bleed/crop (CMYK) + source file (AI or InDesign)
• If possible, provide editable template for future staff cards

Timeline:
• First draft within 5–7 days
• 2 rounds of revisions included

Budget:
$300 USD (total for both brochure + business card)

I’ll provide finalized copy if you accept the project.
Project description (paste this whole block in that box)

We need a premium tri-fold brochure (8.5”×11” letter, folded) and a new business card design for Kestrel Fitness. This will be presented to golf course managers and members, so the look must be elegant, restrained, and country-club-classy.

Scope — Brochure
• Format: Tri-fold, 8.5”×11”. Please set 0.125” bleed on all sides and keep critical text ≥0.125–0.25” inside the trim.
• Purpose: Promote Kestrel Fitness’ golf-specific services for adults 50+.
• Copy: We will provide finalized copy in a Word doc after acceptance. No rewriting needed — please focus on layout and polish.
• Imagery (required):
• Golf-first images (ball on tee/green, mature golfers mid-swing, and golf course landscapes at golden hour).
• 1–2 real Kestrel Fitness gym photos on inside panels (trainer with client doing golf-relevant movement: stretch, rotation, balance).
• Visual style: Premium, quiet, lots of white/negative space, balanced grids; no clutter.
• Brand colors (required): Hunter Green #0C2E1F, Gold #CBA135, Cream #F5F2EB. Convert for CMYK print while preserving the look.
• Typography: Clean, legible serif + sans pairing (e.g., modern serif for headlines, humanist/neo-grotesk sans for body). You may propose suitable professional fonts; avoid playful/novelty fonts.
• Elements to include:
• Our logo (we will upload).
• QR code placement to booking page (we will supply the URL / QR asset).
• Simple icon treatment for the three complimentary options (Strength & Mobility, Stretch Therapy, Vitrascan + Assessment).
• Deliverables:
• Print-ready PDF (CMYK, with bleed & crop marks, PDF/X-1a or PDF/X-4)
• High-res digital PDF (no bleed)
• Source file (InDesign or Illustrator) + packaged fonts/links or outlined type as appropriate.

Scope — Business Card
• Size: 3.5”×2” (US standard) with 0.125” bleed; keep text ≥0.125” from trim.
• Front/back design; consistent with brochure branding.
• Fields: Name, Title, Phone, Email, Website, Address; optional small QR on back.
• Deliverables: Print-ready PDF (CMYK, bleed & crops) + Source file (AI/INDD). Provide an editable template for staff names.

Process & Timing
• Initial concept for brochure + card within 5–7 days of acceptance.
• 2 rounds of revisions included.
• Please start with a clean layout concept using placeholder images/text blocks; we’ll drop in final copy/assets immediately after acceptance.

Stock & Licensing
• You may propose stock images that fit the brief (we’re fine approving Pixelgrove or equivalent). Please note any license fees separately if needed.

Usage Rights
• We require full usage rights to the final designs for print & digital.

Target Market(s)

Golfers 50+ in Victoria, BC: quality-oriented, health-conscious, want to play longer, stronger, and pain-free. Country-club aesthetic; expect polished, professional materials.

Industry/Entity Type

Health & Fitness — Golf Performance / Longevity Studio

Font styles to use
Serif
Sans Serif

Requirements
Must have
• • Golf-first imagery + 1–2 real Kestrel Fitness photos inside. • Brand colors: #0C2E1F (Hunter Green), #CBA135 (Gold), #F5F2EB (Cream). • Premium, restrained layout; ample negative space; no clutter. • Clean professional serif + sans type pairing; highly legible. • Space for logo and QR code (booking). • Correct print specs (bleed, crops, CMYK). • Deliverables: print-ready PDFs (brochure + card), digital PDF, source files.
Nice to have
• • Subtle texture or grain in backgrounds (very light) to add sophistication. • A second brochure cover variation (ball on tee vs. course landscape) at concept stage.
Should not have
• • Cheesy/posed “stocky” groups; overly young models; beer/alcohol imagery. • Over-saturated greens/blues; gimmicky gradients or clip art. • Generic fitness/bodybuilding shots unrelated to golf performance.

```html
<!DOCTYPE html>
<html lang="en">
<head>
<meta charset="utf-8">
<title>Kestrel Fitness – Business Card</title>
<link rel="stylesheet" href="https://fonts.googleapis.com/css2?family=Playfair+Display:wght@500&family=Poppins:wght@300;400;500&display=swap">
<style>
  :root {
    --hunter: #0b2a1c;
    --hunter-ink: #0c2e1f;
    --gold: #c5a356;
    --gold-line: #cba135;
    --white: #ffffff;
    --backdrop: #6f6f6f;
    --text-dark: #2b2b2b;
  }
  * { margin: 0; padding: 0; box-sizing: border-box; }
  html, body { width: 1200px; height: 1029px; overflow: hidden; background: var(--backdrop); }
  body { position: relative; font-family: "Poppins", sans-serif; }

  .card {
    position: absolute;
    left: 262px;
    width: 724px;
    height: 414px;
    overflow: hidden;
    box-shadow: 0 6px 22px rgba(0,0,0,0.28);
  }
  .card--front { top: 74px; }
  .card--back { top: 541px; background: var(--white); }
  .card svg.shapes { position: absolute; inset: 0; }

  .wordmark {
    position: absolute;
    display: flex;
    flex-direction: column;
    align-items: center;
    gap: 10px;
    transform: translate(-50%, -50%);
    font-family: "Poppins", sans-serif;
    font-weight: 500;
    font-size: 17px;
    letter-spacing: 3px;
    text-align: center;
    line-height: 1.2;
  }
  .wordmark__dot { width: 16px; height: 16px; border-radius: 50%; }
  .card--front .wordmark { left: 362px; top: 138px; color: var(--hunter-ink); }
  .card--front .wordmark__dot { background: var(--hunter-ink); }
  .card--back .wordmark { left: 146px; top: 207px; color: var(--white); }
  .card--back .wordmark__dot { background: var(--white); }

  .values {
    position: absolute;
    top: 312px;
    left: 0;
    width: 100%;
    display: flex;
    justify-content: center;
    gap: 16px;
    padding-left: 1px;
  }
  .values__pill {
    width: 166px;
    height: 49px;
    border: 2px solid var(--gold);
    border-radius: 25px;
    color: var(--white);
    font-weight: 300;
    font-size: 23px;
    display: flex;
    align-items: center;
    justify-content: center;
  }

  .person {
    position: absolute;
    left: 335px;
    top: 70px;
  }
  .person__name {
    font-family: "Playfair Display", serif;
    font-weight: 500;
    font-size: 40px;
    color: var(--hunter-ink);
    line-height: 1.1;
    white-space: nowrap;
  }
  .person__title {
    margin-top: 4px;
    font-size: 19px;
    letter-spacing: 2.6px;
    color: var(--gold);
    white-space: nowrap;
  }

  .contact {
    position: absolute;
    left: 364px;
    top: 207px;
    list-style: none;
  }
  .contact li {
    height: 53px;
    font-size: 25px;
    font-weight: 400;
    color: var(--text-dark);
    line-height: 36px;
  }
</style>
</head>
<body>

  <section class="card card--front" aria-label="Business card front">
    <svg class="shapes" width="724" height="414" viewBox="0 0 724 414" role="img" aria-label="Deep green lower band with a subtle textured pattern, gold upper band with a curved bay">
      <rect x="0" y="0" width="724" height="414" fill="var(--hunter)"/>
      <path d="M0 0 H724 V208 H484 A148 148 0 0 1 240 208 H0 Z" fill="var(--gold)"/>
    </svg>
    <div class="wordmark">
      <span class="wordmark__dot"></span>
      <span>KESTREL<br>FITNESS</span>
    </div>
    <div class="values">
      <span class="values__pill">STRENGTH</span>
      <span class="values__pill">MOBILITY</span>
      <span class="values__pill">LONGEVITY</span>
    </div>
  </section>

  <section class="card card--back" aria-label="Business card back">
    <svg class="shapes" width="724" height="414" viewBox="0 0 724 414">
      <rect x="0" y="0" width="292" height="414" fill="var(--hunter)" role="img" aria-label="Deep green panel with a subtle textured pattern"/>
      <rect x="292" y="0" width="8" height="414" fill="var(--gold)"/>
      <rect x="300" y="0" width="12" height="414" fill="var(--hunter)"/>
      <path d="M292 183 C300 183 304 190 318 194 C334 198 338 204 338 214 V360 C338 366 334 371 318 371 H292 Z" fill="var(--gold)"/>
      <!-- phone -->
      <g transform="translate(320 225)" fill="none" stroke="var(--hunter-ink)" stroke-width="2" stroke-linecap="round" stroke-linejoin="round">
        <path d="M-7 -7 L-3 -8 L-1 -3 L-3 -1 C-2 2 1 5 3 6 L5 4 L9 6 L8 9 C1 10 -8 1 -7 -7 Z" fill="var(--hunter-ink)"/>
        <path d="M2 -7 A6 6 0 0 1 8 -1"/>
        <path d="M2 -3 A3 3 0 0 1 4 -1"/>
      </g>
      <!-- envelope -->
      <g transform="translate(320 279)" stroke-linejoin="round">
        <rect x="-9" y="-6" width="18" height="13" fill="var(--hunter-ink)"/>
        <path d="M-9 -6 L0 2 L9 -6" fill="none" stroke="var(--gold)" stroke-width="1.5"/>
      </g>
      <!-- globe -->
      <g transform="translate(320 332)" fill="none" stroke="var(--hunter-ink)" stroke-width="1.8">
        <circle r="9" fill="var(--hunter-ink)"/>
        <ellipse rx="4" ry="9" stroke="var(--gold)" stroke-width="1.2"/>
        <line x1="-9" y1="0" x2="9" y2="0" stroke="var(--gold)" stroke-width="1.2"/>
      </g>
    </svg>
    <div class="wordmark">
      <span class="wordmark__dot"></span>
      <span>KESTREL<br>FITNESS</span>
    </div>
    <div class="person">
      <h1 class="person__name">Anna-Lee Morton</h1>
      <p class="person__title">OWNER KESTREL FITNESS</p>
    </div>
    <ul class="contact">
      <li>250-555-0147</li>
      <li>info@kestrelfitness.biz</li>
      <li>www.kestrelfitness.biz</li>
    </ul>
  </section>

</body>
</html>
```